Stylish Business Cards Wanted

- DOUBLE SIDED Design Required -

High end, edgy cards for a corporate and personal stylist. Must include logo,
Name: Belinda Harwick
Title: Director and Stylist
telephone : +61 8 7142 5809
email: belinda@theloombriefing.example
website: theloombriefing.example
Tag: Corporate Workwear & Uniform Specialist | Personal Stylist
Would like nice icons for telephone, email, website

Target Market(s)

Businesses wanting stylish uniforms, people wanting stylish wardrobes

Industry/Entity Type

Corporate Workwear Stylist

Contact Information for Business Card

I would like black, white and gold foiling incorporated in the design - possibly a touch of the other colours on my branding guide attached Name: Belinda Harwick Title: Director and Stylist telephone : +61 8 7142 5809 email: belinda@theloombriefing.example website: theloombriefing.example Tag: Corporate Workwear & Uniform Specialist | Personal Stylist Would like nice icons for telephone, email, website

Font styles to use
Other font styles liked:
• Raleway

Colors

Designer to choose colors to be used in the design.

Requirements
Must have
• Gold foil accents

```html
<!DOCTYPE html>
<html lang="en">
<head>
<meta charset="utf-8">
<title>The Loom Briefing – Business Card</title>
<link href="https://fonts.googleapis.com/css2?family=Arimo:wght@400&display=swap" rel="stylesheet">
<style>
  :root {
    --page: #e4e2df;
    --card: #f4f2ef;
    --ink: #333132;
    --gold: #e6b94a;
    --band-text: #ffffff;
  }
  html, body {
    margin: 0;
    padding: 0;
    width: 1200px;
    height: 961px;
    overflow: hidden;
    background: var(--page);
    font-family: "Arimo", Arial, sans-serif;
  }
  .card {
    position: absolute;
    left: 100px;
    top: 196px;
    width: 1000px;
    height: 568px;
    background: var(--card);
    border-radius: 10px;
    overflow: hidden;
    box-shadow: 0 10px 30px rgba(0,0,0,0.12);
    color: var(--ink);
  }
  .brand {
    position: absolute;
    left: 200px;
    top: 250px;
    width: 268px;
    text-align: center;
    display: flex;
    align-items: center;
    justify-content: center;
    gap: 10px;
  }
  .brand-mark {
    width: 12px;
    height: 12px;
    background: var(--gold);
    flex: none;
  }
  .brand-name {
    font-size: 25px;
    letter-spacing: 3px;
    color: var(--ink);
    white-space: nowrap;
  }
  .divider {
    position: absolute;
    left: 562px;
    top: 160px;
    width: 2px;
    height: 238px;
    background: var(--ink);
  }
  .contact {
    position: absolute;
    left: 603px;
    top: 162px;
  }
  .role {
    font-size: 27px;
    margin: 0 0 38px;
    font-weight: 400;
    letter-spacing: 0.3px;
  }
  .contact-list {
    list-style: none;
    margin: 0;
    padding: 0;
  }
  .contact-item {
    display: flex;
    align-items: center;
    gap: 12px;
    height: 22px;
    margin-bottom: 18px;
    font-size: 21px;
  }
  .contact-item svg {
    width: 22px;
    height: 22px;
    flex: none;
    margin-left: -2px;
  }
  .footer-band {
    position: absolute;
    left: 0;
    bottom: 0;
    width: 1000px;
    height: 45px;
  }
  .address {
    position: absolute;
    left: 58px;
    top: 535px;
    font-size: 17px;
    color: var(--band-text);
  }
</style>
</head>
<body>
  <div class="card">
    <div class="brand">
      <span class="brand-mark"></span>
      <span class="brand-name">THE LOOM BRIEFING</span>
    </div>

    <div class="divider"></div>

    <div class="contact">
      <h2 class="role">YOUR TITLE</h2>
      <ul class="contact-list">
        <li class="contact-item">
          <svg viewBox="0 0 24 24" aria-hidden="true"><path fill="#333132" d="M6.6 2.5l3 3.6-1.8 2.3c1.2 2.6 3.2 4.7 5.8 5.9l2.3-1.8 3.6 3-1.6 3.3c-.3.6-1 .9-1.6.7C9.6 17.7 5.3 13.4 3.5 6.7c-.2-.6.1-1.3.7-1.6z"/></svg>
          <span>123 456 7890</span>
        </li>
        <li class="contact-item">
          <svg viewBox="0 0 24 24" aria-hidden="true"><rect x="6" y="2" width="12" height="20" rx="2" fill="none" stroke="#333132" stroke-width="2"/><circle cx="12" cy="18.5" r="1.2" fill="#333132"/></svg>
          <span>123 465 7890</span>
        </li>
        <li class="contact-item">
          <svg viewBox="0 0 24 24" aria-hidden="true"><rect x="2" y="6" width="20" height="13" fill="#333132"/><path d="M2 6l10 8 10-8" fill="none" stroke="#f4f2ef" stroke-width="1.5"/></svg>
          <span>hello@uremail.com</span>
        </li>
        <li class="contact-item">
          <svg viewBox="0 0 24 24" aria-hidden="true"><g fill="none" stroke="#333132" stroke-width="1.5"><circle cx="12" cy="12" r="9.5"/><ellipse cx="12" cy="12" rx="4.5" ry="9.5"/><path d="M2.5 12h19M4 7h16M4 17h16M12 2.5v19"/></g></svg>
          <span>www.urwebsite.com</span>
        </li>
      </ul>
    </div>

    <svg class="footer-band" viewBox="0 0 1000 45" preserveAspectRatio="none" aria-hidden="true">
      <path d="M0 2 H380 C420 2 440 14 470 24 L1000 24 V45 H0 Z" fill="#333132"/>
      <path d="M449 12 L1000 12 L1000 22 L478 22 Z" fill="#e6b94a"/>
    </svg>
    <div class="address">48 Tenterden Rd Norwood, SA, AU</div>
  </div>
</body>
</html>
```